Local Roofing/Construction company business needs new biz card design

We need a new business card design, current cards are from the start of this operation and generic at best. We are a local Construction Company (General Contractor) with a majority of our work originating from insurance claims-exterior finish work is the main focus (Roofs-Siding-Gutters etc). Heavily involved with homeowners and the low ball offers they receive from insurance company's after a insurable event takes place. I have attached some of our original logo file(s) below.

```html
<!DOCTYPE html>
<html lang="en">
<head>
<meta charset="utf-8">
<title>Ridgeway Builders – Business Card</title>
<link href="https://fonts.googleapis.com/css2?family=Archivo:wght@400;500;700;800&display=swap" rel="stylesheet">
<style>
  :root {
    --green: #4cb86a;
    --green-mid: #2f7a4c;
    --ink: #0c2226;
    --text: #2c2c2c;
    --muted: #555;
    --paper: #ffffff;
    --backdrop: #e9ebe8;
  }
  * { box-sizing: border-box; margin: 0; padding: 0; }
  html, body { width: 1200px; height: 900px; overflow: hidden; }
  body {
    background: var(--backdrop);
    font-family: "Archivo", Arial, sans-serif;
    display: flex; flex-direction: column; align-items: center; justify-content: center;
    gap: 36px;
  }
  .card {
    position: relative; width: 700px; height: 400px; border-radius: 28px; overflow: hidden;
    box-shadow: 0 10px 30px rgba(0,0,0,.18);
  }

  /* back side */
  .card--back {
    background: radial-gradient(circle at 18% 85%, #4fbd6c 0%, #3a9a58 30%, #1f5a3c 62%, var(--ink) 100%);
    color: var(--ink);
  }
  .brand-badge {
    position: absolute; top: 44px; right: 44px;
    display: flex; align-items: center; gap: 12px;
    background: var(--green); border-radius: 18px; padding: 22px 24px;
  }
  .brand-badge__square { width: 22px; height: 22px; background: var(--ink); }
  .brand-badge__name {
    font-weight: 800; font-size: 26px; line-height: 1.05; text-transform: uppercase; color: var(--ink);
  }
  .back-info { position: absolute; left: 56px; bottom: 50px; width: 420px; }
  .tagline {
    font-size: 13.5px; font-weight: 500; letter-spacing: .3px; text-transform: uppercase;
    padding-bottom: 8px; border-bottom: 1.5px solid var(--ink); margin-bottom: 12px; width: 520px;
  }
  .hours { font-size: 17px; line-height: 1.35; }
  .hours span { color: #fff; }
  .emergency { display: flex; align-items: center; gap: 12px; margin-top: 12px; font-size: 24px; }
  .emergency span { color: #fff; }
  .emergency svg { width: 24px; height: 24px; }

  /* front side */
  .card--front { background: linear-gradient(135deg, #eeeeee 0%, var(--paper) 55%); color: var(--text); }
  .person { position: absolute; left: 48px; top: 70px; }
  .person__name { color: var(--green); font-weight: 700; font-size: 24px; text-transform: uppercase; }
  .person__role { font-size: 17px; color: var(--muted); margin-top: 2px; }
  .contacts { list-style: none; margin-top: 18px; margin-left: 20px; }
  .contacts li { display: flex; align-items: flex-start; gap: 12px; font-size: 18px; line-height: 1.3; margin-bottom: 3px; color: var(--text); }
  .contacts svg { width: 18px; height: 18px; flex: none; margin-top: 3px; fill: var(--green); }
  .divider { position: absolute; left: 0; top: 300px; width: 430px; height: 2px; background: var(--green); }
  .brand-band {
    position: absolute; left: 80px; bottom: 28px;
    display: flex; align-items: center; gap: 16px;
    background: var(--ink); border-radius: 14px; padding: 18px 30px;
  }
  .brand-band__square { width: 26px; height: 26px; background: var(--green); }
  .brand-band__name { color: #fff; font-weight: 800; font-size: 34px; text-transform: uppercase; letter-spacing: .5px; }
  .services { position: absolute; right: 44px; top: 120px; text-align: right; }
  .services__title { color: var(--green); font-weight: 700; font-size: 20px; text-transform: uppercase; margin-bottom: 6px; }
  .services ul { list-style: none; }
  .services li { display: flex; justify-content: flex-end; align-items: center; gap: 8px; font-size: 17px; line-height: 1.5; color: var(--muted); }
  .services svg { width: 15px; height: 15px; fill: var(--green); }
</style>
</head>
<body>

<section class="card card--back">
  <div class="brand-badge">
    <div class="brand-badge__square"></div>
    <div class="brand-badge__name">Ridgeway<br>Builders</div>
  </div>
  <div class="back-info">
    <p class="tagline">You can trust our 30 years of combined experience</p>
    <p class="hours">Monday - Friday: <span>8am - 6pm</span><br>Saturday - Sunday: <span>By Appointment Only</span></p>
    <p class="emergency">
      <svg viewBox="0 0 24 24"><path fill="#0c2226" d="M6.6 10.8a15.1 15.1 0 0 0 6.6 6.6l2.2-2.2a1 1 0 0 1 1-.25 11.4 11.4 0 0 0 3.6.57 1 1 0 0 1 1 1V20a1 1 0 0 1-1 1A17 17 0 0 1 3 4a1 1 0 0 1 1-1h3.5a1 1 0 0 1 1 1c0 1.25.2 2.45.57 3.57a1 1 0 0 1-.25 1z"/></svg>
      Emergency: <span>555-201-7740</span>
    </p>
  </div>
</section>

<section class="card card--front">
  <div class="person">
    <h1 class="person__name">Daniel Reyes</h1>
    <p class="person__role">Director</p>
    <ul class="contacts">
      <li><svg viewBox="0 0 24 24"><path d="M6.6 10.8a15.1 15.1 0 0 0 6.6 6.6l2.2-2.2a1 1 0 0 1 1-.25 11.4 11.4 0 0 0 3.6.57 1 1 0 0 1 1 1V20a1 1 0 0 1-1 1A17 17 0 0 1 3 4a1 1 0 0 1 1-1h3.5a1 1 0 0 1 1 1c0 1.25.2 2.45.57 3.57a1 1 0 0 1-.25 1z"/></svg>555-201-3368</li>
      <li><svg viewBox="0 0 24 24"><path d="M2 5h20v14H2z M2 5l10 8 10-8" stroke="#fff" stroke-width="1.5"/></svg>office@ridgewaybuilders.com</li>
      <li><svg viewBox="0 0 24 24"><circle cx="12" cy="12" r="10"/><path d="M2 12h20M12 2c3 3 3 17 0 20M12 2c-3 3-3 17 0 20" stroke="#fff" stroke-width="1.3" fill="none"/></svg>www.ridgewaybuilders.com</li>
      <li><svg viewBox="0 0 24 24"><path d="M12 2a7 7 0 0 0-7 7c0 5 7 13 7 13s7-8 7-13a7 7 0 0 0-7-7zm0 9.5A2.5 2.5 0 1 1 12 6.5a2.5 2.5 0 0 1 0 5z"/></svg>48 Orchard Hill Rd,<br>Fairbrook, MO 63012</li>
    </ul>
  </div>
  <div class="divider"></div>

  <div class="services">
    <h2 class="services__title">Our Services</h2>
    <ul>
      <li>Residential Roofing <svg viewBox="0 0 16 16"><path d="M8 1 1 7.5h2V15h10V7.5h2z"/></svg></li>
      <li>Commercial Roofing <svg viewBox="0 0 16 16"><path d="M8 1 1 7.5h2V15h10V7.5h2z"/></svg></li>
      <li>Storm Restoration <svg viewBox="0 0 16 16"><path d="M8 1 1 7.5h2V15h10V7.5h2z"/></svg></li>
      <li>Exterior Finishes <svg viewBox="0 0 16 16"><path d="M8 1 1 7.5h2V15h10V7.5h2z"/></svg></li>
    </ul>
  </div>

  <div class="brand-band">
    <div class="brand-band__square"></div>
    <div class="brand-band__name">Ridgeway Builders</div>
  </div>
</section>

</body>
</html>
```